Qvx Brightforge Website

All the descriptions are available in the attached file. The designer has to structure the website and find the right images and icons. The website should look modern and avoid using images of real humans rather use animated images. Please note that the design should include home page, all the 4 services page , the contact us would be at the bottom of home page.

```html
<!DOCTYPE html>
<html lang="en">
<head>
<meta charset="utf-8">
<title>Qvx Brightforge</title>
<link href="https://fonts.googleapis.com/css2?family=Poppins:wght@300;400;500;600;700&display=swap" rel="stylesheet">
<style>
:root{
  --blue:#1b7ae0;
  --orange:#f39200;
  --green:#6ab023;
  --ink:#2b2b2b;
  --muted:#6f6f6f;
  --grey-bg:#f1f1f1;
  --peach:#fdf0df;
  --sky:#e7f0fb;
  --footer:#262626;
  --white:#ffffff;
}
*{margin:0;padding:0;box-sizing:border-box}
html,body{width:1200px;height:2644px;overflow:hidden}
body{font-family:"Poppins",sans-serif;color:var(--ink);background:var(--white);position:relative}
a{text-decoration:none;color:inherit}

/* header */
.site-header{position:absolute;top:0;left:0;width:1200px;height:90px;z-index:3}
.brand{position:absolute;left:40px;top:26px;display:flex;align-items:center;gap:10px;font-weight:700;font-size:26px;color:var(--blue)}
.brand-mark{width:18px;height:18px;background:var(--orange)}
.main-nav{position:absolute;right:200px;top:38px;display:flex;gap:44px;font-size:14px;font-weight:500;color:var(--ink)}
.main-nav .active{color:var(--blue);position:relative}
.main-nav .active::after{content:"";position:absolute;left:0;right:0;bottom:-8px;height:3px;background:var(--orange)}
.btn-login{position:absolute;right:40px;top:26px;background:var(--blue);color:var(--white);font-size:14px;font-weight:600;padding:12px 28px;border-radius:3px}

/* hero */
.hero{position:absolute;top:0;left:0;width:1200px;height:640px}
.hero-deco{position:absolute;left:0;top:90px}
.hero-copy{position:absolute;left:120px;top:220px;width:500px}
.hero-copy .eyebrow{font-size:28px;font-weight:500;color:var(--ink);letter-spacing:1px}
.hero-copy h1{margin-top:24px;font-size:44px;font-weight:700;color:var(--blue);letter-spacing:1px;line-height:1;white-space:nowrap}
.hero-copy h1 span{background:var(--orange);color:var(--white);padding:8px 10px}
.btn-outline{display:inline-block;border:2px solid var(--blue);color:var(--blue);font-size:14px;font-weight:500;padding:12px 24px;border-radius:3px}
.hero-copy .btn-outline{margin-top:70px}
.hero-art{position:absolute;left:640px;top:100px}
.hero-dots{position:absolute;left:572px;top:546px;display:flex;gap:8px}
.hero-dots i{width:10px;height:10px;border-radius:50%;background:var(--blue);display:block}
.hero-dots i:last-child{background:var(--orange)}

/* section titles */
.section-title{font-size:36px;font-weight:600;color:var(--blue);letter-spacing:1px;display:inline-flex;align-items:flex-start;gap:8px}
.title-mark{display:grid;grid-template-columns:12px 12px;gap:3px;margin-top:-6px}
.title-mark i{width:12px;height:12px;display:block}
.title-mark i:nth-child(1){background:transparent}
.title-mark i:nth-child(2){background:var(--blue)}
.title-mark i:nth-child(3){background:var(--orange)}
.title-mark i:nth-child(4){background:var(--green)}

/* about */
.about{position:absolute;top:670px;left:0;width:1200px;height:580px;background:var(--grey-bg)}
.about-deco{position:absolute;left:0;top:0;width:60px;height:200px;background:#e3eed6}
.about-art{position:absolute;left:70px;top:90px;width:440px;height:360px;border-radius:8px;background:linear-gradient(135deg,#dbe9fb,#fbe4c4)}
.about-copy{position:absolute;left:596px;top:60px;width:560px}
.about-copy p{margin-top:24px;font-size:15.5px;line-height:1.78;color:var(--muted);font-weight:300}
.btn-orange-outline{display:inline-block;margin-top:34px;border:2px solid var(--orange);color:var(--orange);font-size:14px;font-weight:500;padding:11px 22px;border-radius:3px}

/* services */
.services{position:absolute;top:1250px;left:0;width:1200px;height:540px}
.services .section-title{position:absolute;left:435px;top:18px}
.service-grid{position:absolute;top:110px;left:0;width:1200px;height:420px;display:grid;grid-template-columns:repeat(4,300px)}
.service-card{padding:30px 28px;text-align:center}
.service-card:nth-child(odd){background:var(--peach)}
.service-card:nth-child(even){background:var(--sky)}
.service-art{width:220px;height:140px;margin:0 auto;border-radius:6px}
.service-card:nth-child(odd) .service-art{background:linear-gradient(135deg,#cfe1f8,#f8cf94)}
.service-card:nth-child(even) .service-art{background:linear-gradient(135deg,#bcd6f5,#f6d7ae)}
.service-card h3{margin-top:26px;font-size:17px;font-weight:600;color:var(--ink);letter-spacing:.5px}
.service-card p{margin-top:14px;font-size:12px;line-height:1.7;color:var(--muted)}
.service-card .more{display:inline-block;margin-top:16px;font-size:12px;font-weight:600;color:var(--orange)}

/* contact */
.contact{position:absolute;top:1790px;left:0;width:1200px;height:510px}
.contact .section-title{position:absolute;left:460px;top:40px}
.contact-list{position:absolute;left:110px;top:130px;list-style:none}
.contact-item{display:flex;gap:26px;margin-bottom:32px}
.contact-icon{width:40px;height:40px;flex:none}
.contact-item h4{font-size:18px;font-weight:500;letter-spacing:.5px}
.contact-item p{font-size:12px;color:var(--muted);margin-top:2px}
.contact-form{position:absolute;left:530px;top:130px;width:400px}
.form-row{display:flex;gap:40px;margin-bottom:30px}
.field{flex:1;font-size:12px;color:var(--ink);border-bottom:1px solid #cfcfcf;padding-bottom:10px}
.field.message{height:64px}
.btn-submit{display:inline-block;background:var(--orange);color:var(--white);font-size:13px;font-weight:600;padding:12px 22px;border-radius:2px}

/* footer */
.site-footer{position:absolute;top:2300px;left:0;width:1200px;height:344px;background:var(--footer);text-align:center;color:var(--white)}
.footer-brand{margin-top:50px;display:inline-flex;align-items:center;gap:10px;font-size:30px;font-weight:700;color:var(--white)}
.footer-brand .brand-mark{width:20px;height:20px}
.footer-nav{margin-top:66px;display:flex;justify-content:center;gap:70px;font-size:13px;font-weight:500}
.social{margin-top:34px;display:flex;justify-content:center;gap:12px}
.social i{width:28px;height:28px;border:2px solid var(--orange);border-radius:50%;display:block}
.copyright{margin-top:18px;font-size:13px;font-weight:500}
</style>
</head>
<body>

<section class="hero">
  <svg class="hero-deco" width="60" height="160" viewBox="0 0 60 160" aria-hidden="true">
    <rect x="0" y="0" width="44" height="44" fill="#6ab023"/>
    <rect x="0" y="60" width="28" height="90" fill="#f39200"/>
  </svg>
  <div class="hero-copy">
    <p class="eyebrow">WELCOME TO</p>
    <h1><span>QVX</span> BRIGHTFORGE</h1>
    <a class="btn-outline" href="#">GET STARTED</a>
  </div>
  <svg class="hero-art" width="560" height="460" viewBox="0 0 560 460">
    <defs>
      <linearGradient id="heroGrad" x1="0" y1="0" x2="1" y2="1">
        <stop offset="0" stop-color="#ffd28a"/>
        <stop offset="1" stop-color="#6aa8ec"/>
      </linearGradient>
    </defs>
    <path d="M80 0 H560 V330 C560 430 480 470 400 440 C320 410 270 470 180 450 C80 430 20 360 40 270 C60 180 0 130 30 60 C45 20 60 0 80 0 Z" fill="#f39200"/>
    <path role="img" aria-label="Isometric illustration of a person working beside data dashboards and charts" d="M120 40 H520 V320 C520 390 460 410 400 390 C330 365 290 420 210 405 C130 390 90 330 105 260 C120 190 80 150 100 90 Z" fill="url(#heroGrad)"/>
  </svg>
  <div class="hero-dots"><i></i><i></i><i></i></div>
</section>

<header class="site-header">
  <a class="brand" href="#"><span class="brand-mark"></span>Qvx Brightforge</a>
  <nav class="main-nav">
    <a class="active" href="#">HOME</a>
    <a href="#">SERVICES ▾</a>
    <a href="#">PRODUCTS</a>
    <a href="#">BLOG</a>
    <a href="#">CONTACT US</a>
  </nav>
  <a class="btn-login" href="#">LOG IN</a>
</header>

<section class="about">
  <div class="about-deco"></div>
  <div class="about-art" role="img" aria-label="Illustration of a team analysing charts, gears and growth graphs"></div>
  <div class="about-copy">
    <h2 class="section-title">ABOUT US <span class="title-mark"><i></i><i></i><i></i><i></i></span></h2>
    <p>We are a forward-thinking IT consultancy firm specializing in providing cutting-edge data analytics, web application development, and mobile app development services. Our passion for innovation and technology drives us to deliver tailor-made solutions that empower businesses to thrive in the digital landscape. We take pride in our ability to collaborate with early-stage startups as their technology partner, helping them navigate the challenges of launching and scaling their ventures. Our team of experienced professionals works closely with clients, understanding their unique requirements and goals, to craft bespoke solutions that propel growth and foster success.</p>
    <a class="btn-orange-outline" href="#">LEARN MORE</a>
  </div>
</section>

<section class="services">
  <h2 class="section-title">OUR SERVICES <span class="title-mark"><i></i><i></i><i></i><i></i></span></h2>
  <div class="service-grid">
    <article class="service-card">
      <div class="service-art" role="img" aria-label="Illustration of data analytics dashboards"></div>
      <h3>DATA ANALYTICS</h3>
      <p>At Qvx Brightforge, our proficiency consists of turning raw business data into clear dashboards and insights that help teams make smarter, faster and more confident decisions.</p>
      <a class="more" href="#">LEARN MORE ›</a>
    </article>
    <article class="service-card">
      <div class="service-art" role="img" aria-label="Illustration of a team building a website"></div>
      <h3>WEB DEVELOPMENT</h3>
      <p>At Qvx Brightforge, we are a collaborative web development company committed to building fast, secure and accessible websites and web apps that grow with your business.</p>
      <a class="more" href="#">LEARN MORE ›</a>
    </article>
    <article class="service-card">
      <div class="service-art" role="img" aria-label="Illustration of mobile app screens being designed"></div>
      <h3>MOBILE APP DEVELOPMENT</h3>
      <p>At Qvx Brightforge, we are a pioneering mobile app development company dedicated to crafting intuitive native and cross-platform apps that users love to open every day.</p>
      <a class="more" href="#">LEARN MORE ›</a>
    </article>
    <article class="service-card">
      <div class="service-art" role="img" aria-label="Illustration of two partners agreeing on a startup plan"></div>
      <h3>STARTUP PARTNER</h3>
      <p>At Qvx Brightforge, we are committed to supporting early-stage start-ups as their technology partner, from first prototype to a scalable product ready for growth.</p>
      <a class="more" href="#">LEARN MORE ›</a>
    </article>
  </div>
</section>

<section class="contact">
  <h2 class="section-title">CONTACT US <span class="title-mark"><i></i><i></i><i></i><i></i></span></h2>
  <ul class="contact-list">
    <li class="contact-item">
      <svg class="contact-icon" viewBox="0 0 40 40" aria-hidden="true"><path d="M20 4c-6.6 0-12 5.2-12 11.6C8 24 20 36 20 36s12-12 12-20.4C32 9.2 26.6 4 20 4z" fill="none" stroke="#2b2b2b" stroke-width="2.5"/><circle cx="20" cy="15.5" r="4.5" fill="none" stroke="#2b2b2b" stroke-width="2.5"/></svg>
      <div><h4>ADDRESS</h4><p>Suite 18, 42 Harbour Lane, Northfield<br>3021</p></div>
    </li>
    <li class="contact-item">
      <svg class="contact-icon" viewBox="0 0 40 40" aria-hidden="true"><path d="M11 5l6 7-3.5 4c1.8 4 5 7.2 9 9l4-3.5 7 6-3.5 5C18 34 6 22 6 8.5z" fill="none" stroke="#2b2b2b" stroke-width="2.5" stroke-linejoin="round"/></svg>
      <div><h4>PHONE</h4><p>+1 555 0142 378</p></div>
    </li>
    <li class="contact-item">
      <svg class="contact-icon" viewBox="0 0 40 40" aria-hidden="true"><rect x="5" y="9" width="30" height="22" rx="2" fill="none" stroke="#2b2b2b" stroke-width="2.5"/><path d="M6 11l14 11 14-11" fill="none" stroke="#2b2b2b" stroke-width="2.5"/></svg>
      <div><h4>EMAIL</h4><p>hello@qvxbrightforge.com</p></div>
    </li>
  </ul>
  <form class="contact-form">
    <div class="form-row"><div class="field">First Name :</div><div class="field">Last Name :</div></div>
    <div class="form-row"><div class="field">Email :</div><div class="field">Phone :</div></div>
    <div class="form-row"><div class="field message">Message :</div></div>
    <span class="btn-submit">SUBMIT</span>
  </form>
</section>

<footer class="site-footer">
  <div class="footer-brand"><span class="brand-mark"></span>Qvx Brightforge</div>
  <nav class="footer-nav">
    <a href="#">HOME</a><a href="#">SERVICES</a><a href="#">PRODUCTS</a><a href="#">BLOG</a><a href="#">CONTACT US</a>
  </nav>
  <div class="social"><i></i><i></i><i></i><i></i><i></i></div>
  <p class="copyright">©Copyrights 2023 Qvx Brightforge &nbsp;|&nbsp; All Rights Reserved</p>
</footer>

</body>
</html>
```